Quill Harbor (IT/Network Services)

Quill Harbor, LLC provides technology services to small and medium businesses. Essentially, anytime you've every thought your business might need an "IT guy" to handle something you could instead call us to handle it. Basically, you can outsource your IT needs to us.

This is a brand new company and so we'll need a brand new website. I'd like to use WordPress to handle the site since that will make things easier for me to maintain in the long run.

The site should include a, more-or-less, static front page with the dynamic data occurring on pages linked from a navigational area.

I have a logo already designed that I would like to see used in the design. The one with "white" in the title is the official logo, just added some other versions for your perusal.

Color queues from the logo but feel free to add other colors where applicable.

The site should feel somewhat corporate but with a "younger" slant (something a 25-35 year old would enjoy).

Pages (either to be added initially or by me after design completion):
"About" section - includes company history, business philosophy, etc.
"Services" section - service options, service approach, service specifics
"Testimonials" section - (eventually)
"News" section - (eventually) industry news, company news, events, blog
Contact Links

Websites to view:
The two largest local competitors:
http://www.brightmarsh-tech.example/
http://www.kelvarworks.example/
Other local competitors:
http://www.tpbllc.example/
http://www.morrowfield.example/

Other info you might find useful:
Domain: qhllc.example
Address:
417 Elm Row S
Suite 512B
Nashville, TN 37288
Phone: 615-555-0187
Emails available for use/display:
info@qhllc.example
sales@qhllc.example

Target Market(s)

Our target clients are mainly small businesses (25 or less computer users) which means we're looking at a lot of start-ups or younger companies. We'll be interacting with many entrepreneurs and young business owners.

Requirements
Must have
• Need full WP theme (not a mockup)

```html
<!DOCTYPE html>
<html lang="en">
<head>
<meta charset="utf-8">
<title>Quill Harbor — IT &amp; Network Services</title>
<link rel="stylesheet" href="https://fonts.googleapis.com/css2?family=Source+Sans+3:wght@400;600&display=swap">
<style>
:root{
  --orange:#e98d0b;
  --orange-dark:#c9750a;
  --orange-text:#e8900f;
  --heading:#c2750f;
  --grey-logo:#77787b;
  --body-text:#4a4a4a;
  --side-text:#5a5a5a;
  --nav-top:#5a5a5a;
  --nav-bottom:#151515;
  --white:#ffffff;
  --paper:#fdfcf9;
  --rule:#e3e3e3;
}
*{margin:0;padding:0;box-sizing:border-box}
html,body{width:1200px;height:1158px;overflow:hidden}
body{position:relative;background:var(--orange);font-family:"Source Sans 3",Arial,sans-serif;color:var(--body-text)}
.site-header{position:absolute;left:0;top:0;width:1200px;height:138px;
  background:repeating-linear-gradient(0deg,#f4f5f6 0 2px,#fbfbfc 2px 4px);border-bottom:1px solid #d7d7d7}
.brand{position:absolute;left:134px;top:40px;display:flex;align-items:center;gap:12px}
.brand-dot{width:36px;height:36px;border-radius:50%;background:var(--orange-text)}
.brand-name{font-size:34px;font-weight:600;color:var(--grey-logo);letter-spacing:.5px}
.search{position:absolute;left:869px;top:34px;display:flex}
.search-field{width:184px;height:27px;border:1px solid #cfcfcf;background:#fff}
.search-btn{width:27px;height:27px;background:linear-gradient(#f6a733,#e48a0c);display:flex;align-items:center;justify-content:center}
.social{position:absolute;top:87px;width:27px;height:27px;border-radius:3px}
.social.one{left:1014px;background:#3b5998}
.social.two{left:1054px;background:#2fb6e8}
.main-nav{position:absolute;left:120px;top:138px;width:960px;height:40px;border-radius:0 0 8px 8px;
  background:linear-gradient(var(--nav-top),var(--nav-bottom));box-shadow:0 8px 14px -6px rgba(0,0,0,.45)}
.main-nav a{position:absolute;top:11px;color:#fff;font-size:13px;text-decoration:none;text-shadow:0 1px 1px #000;transform:translateX(-50%)}
.hero{position:absolute;left:120px;top:212px;width:960px;height:380px;background:var(--orange-dark);padding:7px}
.hero-inner{position:relative;width:946px;height:366px;background:var(--paper)}
.hero-title{position:absolute;left:0;width:500px;text-align:center;color:var(--orange-text);font-weight:400;line-height:1}
.hero-title.small{top:104px;font-size:58px;letter-spacing:-1px}
.hero-title.big{top:185px;font-size:64px}
.hero-photo{position:absolute;left:480px;top:0;width:466px;height:366px;
  background:radial-gradient(ellipse at 62% 40%,#c8c8ca 0,#e6e6e7 28%,#fff 60%)}
.hero-arrow{position:absolute;top:370px;width:26px;height:44px;background:#fff;border-radius:6px;
  color:var(--orange);font-size:22px;font-weight:600;display:flex;align-items:center;justify-content:center}
.hero-arrow.prev{left:96px}.hero-arrow.next{left:1078px}
.band-line{position:absolute;left:0;top:608px;width:1200px;height:4px;background:linear-gradient(rgba(0,0,0,.12),rgba(0,0,0,0))}
.content{position:absolute;left:120px;top:645px;width:960px;height:455px;background:var(--white);border-radius:10px;
  box-shadow:0 6px 10px -4px rgba(0,0,0,.35)}
.intro{position:absolute;left:23px;top:14px;width:612px}
.intro h1{font-size:30px;font-weight:400;color:var(--heading);margin-bottom:14px}
.intro p{font-size:12px;line-height:20px;margin-bottom:17px}
.divider{position:absolute;left:644px;top:14px;width:1px;height:420px;background:linear-gradient(#fff,#ddd 20%,#ddd 80%,#fff)}
.sidebar{position:absolute;left:674px;top:24px;width:275px;font-family:Arial,Helvetica,sans-serif}
.sidebar h2{font-family:"Source Sans 3",Arial,sans-serif;font-size:18px;font-weight:400;color:var(--heading);margin-bottom:16px}
.sidebar p{font-size:12px;line-height:14.5px;color:var(--side-text);margin-bottom:19px}
.sidebar cite{font-style:italic;font-weight:bold;color:#333}
.sidebar hr{border:0;height:1px;background:linear-gradient(90deg,#fff,#ddd,#fff);margin:7px 0 22px}
.copyright{position:absolute;left:1043px;top:1110px;font-size:10px;color:#fff;font-family:Arial,sans-serif}
</style>
</head>
<body>
<header class="site-header">
  <div class="brand"><span class="brand-dot"></span><span class="brand-name">Quill Harbor</span></div>
  <div class="search"><div class="search-field"></div><div class="search-btn">
    <svg width="10" height="10" viewBox="0 0 10 10"><circle cx="4" cy="4" r="2.6" fill="none" stroke="#fff" stroke-width="1.6"/><line x1="6" y1="6" x2="9" y2="9" stroke="#fff" stroke-width="1.8"/></svg>
  </div></div>
  <span class="social one" role="img" aria-label="Social profile link"></span>
  <span class="social two" role="img" aria-label="Social profile link"></span>
</header>
<nav class="main-nav">
  <a href="#" style="left:81px">Home</a>
  <a href="#" style="left:210px">About Us</a>
  <a href="#" style="left:339px">Our Clients</a>
  <a href="#" style="left:475px">What We Do</a>
  <a href="#" style="left:621px">News &amp; Events</a>
  <a href="#" style="left:756px">Support</a>
  <a href="#" style="left:873px">Contact</a>
</nav>
<section class="hero">
  <div class="hero-inner">
    <div class="hero-photo" role="img" aria-label="Silver computer mouse with cable"></div>
    <div class="hero-title small">Welcome to</div>
    <div class="hero-title big">QUILL HARBOR</div>
  </div>
</section>
<div class="hero-arrow prev">&#10094;</div>
<div class="hero-arrow next">&#10095;</div>
<div class="band-line"></div>
<main class="content">
  <article class="intro">
    <h1>Welcome</h1>
    <p>Praesent vestibulum aenean Nonummyhendrerit mauris. Hasellus porta. Fusce suscipit varius mi. Cum sociis natoque penatibus et magnis dis parturient montes nascetur ridiculus mus. Nulla dui.&nbsp; etur ridiculus mus. Nulla dui. Praesent vestibulum aenean Nonummyhendrerit mauris. Hasellus porta. Fusce suscipit varius mi. Cum sociis natoque penatibus et magnis dis parturient montes nascetur ridiculus mus. Nulla dui.&nbsp; etur ridiculus mus. Nulla dui. Praesent vestibulum aenean Nonummyhendrerit mauris. Hasellus porta. Fusce suscipit varius mi. Cum sociis natoque penatibus et magnis dis parturient montes nascetur ridiculus mus. Nulla dui.&nbsp; etur ridiculus mus. Nulla dui.</p>
    <p>Praesent vestibulum aenean Nonummyhendrerit mauris. Hasellus porta. Fusce suscipit varius mi. Cum sociis natoque penatibus et magnis dis parturient montes nascetur ridiculus mus. Nulla dui.&nbsp; etur ridiculus mus. Nulla dui.</p>
    <p>Nulla dui.&nbsp; etur ridiculus mus. Nulla dui. Praesent vestibulum aenean Nonummyhendrerit mauris. Hasellus porta. Fusce suscipit varius mi. Cum sociis natoque penatibus et na dui. Praesent vestibulum aenean Nonummyhendrerit mauris. Hasellus porta. Fusce suscipit varius mi. Cum sociis natoque penatibus et magnis dis parturient montes nascetur ridiculus mus. Nulla dui.&nbsp; etur ridiculus mus. Nulla dui. Praesent vestibulum aenean Nonummyhendrerit mauris. Hasellus porta. Fusce suscipit varius mi. Cum sociis natoque penatibus et magnis dis parturient montes nascetur ridiculus mus. Nulla dui.&nbsp; etur ridiculus mus. Nulla dui.</p>
  </article>
  <div class="divider"></div>
  <aside class="sidebar">
    <h2>What our client saying...</h2>
    <p>Lorem ipsum dolor sit amet, consectetur adipiscing elit. Cras laoreet, lacus aliquet sodales mattis, elit ante varius est, sit amet tincidunt quam purus sit amet mi! - <cite>John Smith</cite></p>
    <p>Lorem ipsum dolor sit amet, consectetur adipiscing elit. Cras laoreet, lacus aliquet sodales mattis, elit ante varius est, sit amet tincidunt quam purus sit amet mi! - <cite>John Smith</cite></p>
    <hr>
    <h2>News &amp; Events</h2>
    <p>Lorem ipsum dolor sit amet, consectetur adipiscing elit. Cras laoreet, lacus aliquet sodales mattis, elit ante varius est, sit amet tincidunt quam purus sit amet mi! - <cite>John Smith</cite></p>
    <p>Lorem ipsum dolor sit amet, consectetur adipiscing elit. Cras laoreet, lacus aliquet sodales mattis, elit ante varius est, sit amet tincidunt quam purus sit amet mi! - <cite>John Smith</cite></p>
  </aside>
</main>
<footer class="copyright">© 2012</footer>
</body>
</html>
```